Home decoration company - sustainable wall panels

- I would need you to design 5-10 pages for my client's website.
- The design should have details of wall panels that are being sold on the website - movelterra.com.
- It should have wood + sustainability branding.
- please focus on using shapes of products that are being sold on the website and use them as design for branding

See more here
https://sheets.quorvix.net/d/7kpRtW2nLqZ8bYhMfGcVdXsJ4eTuA9wN3oHiKy5BzPl/edit?usp=sharing

Target Market(s)

people who are want sustainable home/business wall decor

Industry/Entity Type

Interior Decoration

Logo Text

Movel Terra (for favicon, "MT")

Number of Pages Required

5+ page

Font styles to use
Serif
Sans Serif

Requirements
Must have
• - details of products that are being sold on the website movelterra.com (you will see there are different wall panel shapes)
- great creative design ideas
- follow instructions from here https://sheets.quorvix.net/d/7kpRtW2nLqZ8bYhMfGcVdXsJ4eTuA9wN3oHiKy5BzPl/edit?usp=sharing
- the design must be at least 2 levels above the current one on movelterra.com
- use photos from here https://files.quorvix.net/folders/5tWmQeRb8YuNc2XkLpAsDv3ZhGj7FiO-?usp=sharing
Nice to have
• - it would be nice if you would give your own creative suggestions
Should not have
• - should not look like it's a 1990s website

```html
<!DOCTYPE html>
<html lang="en">
<head>
<meta charset="utf-8">
<title>Movel Terra – Table Tops</title>
<link href="https://fonts.googleapis.com/css2?family=Oswald:wght@500;600&family=Poppins:wght@400;500;600;700&display=swap" rel="stylesheet">
<style>
:root{
  --bark:#2b1608;
  --accent:#8a4a10;
  --star:#f2a21d;
  --text:#3a2a20;
  --muted:#6b5b50;
  --footer:#f3f1ef;
  --field:#e4e2e0;
  --line:#cfcac5;
}
*{box-sizing:border-box;margin:0;padding:0}
html,body{width:798px;height:1200px;overflow:hidden;background:#fff}
body{position:relative;font-family:"Poppins",sans-serif;color:var(--text)}
.abs{position:absolute}
.display{font-family:"Oswald",sans-serif;font-weight:600;color:var(--bark);text-transform:uppercase;letter-spacing:-0.2px}

.topbar{left:0;top:0;width:798px;height:19.5px;background:var(--bark);color:#fff;font-size:6.8px}
.topbar .note{left:59px;top:5.5px}
.topbar .contact{right:59px;top:5.5px;display:flex;gap:16px}
.topbar .contact span{display:flex;align-items:center;gap:4px}

.header{left:0;top:19.5px;width:798px;height:46.5px;background:#fff}
.brand{left:58px;top:10px;display:flex;align-items:center;gap:6px}
.brand-mark{width:14px;height:14px;background:var(--bark)}
.brand-name{font-family:"Poppins",sans-serif;font-weight:600;font-size:12px;color:var(--bark)}
.nav{right:59px;top:18px;display:flex;gap:18.5px;font-family:"Oswald",sans-serif;font-weight:500;font-size:8.3px;color:var(--bark);text-transform:uppercase}
.nav .active{color:var(--accent)}

.hero{left:0;top:66px;width:798px;height:144px;background:linear-gradient(90deg,#6a4a30 0%,#4a3020 45%,#3c3a3a 62%,#6a5a50 75%,#5a6a7a 100%)}
.hero-title{left:0;top:122px;width:798px;text-align:center;color:#fff;font-size:24px}

.made-title{left:0;top:268px;width:798px;text-align:center;font-size:24px}
.made-copy{left:155px;top:302px;width:488px;text-align:center;font-size:8.9px;line-height:14.8px;color:var(--text)}

.product-title{left:56px;top:450px;font-size:24px}
.rating{left:56px;top:483px;font-size:11.3px;font-weight:600;color:var(--bark);letter-spacing:.4px;display:flex;align-items:center;gap:4px}
.specs{left:56px;top:506px;width:345px;font-size:9.3px;line-height:13.6px;color:var(--text)}
.specs p{margin-bottom:8px}
.price{left:56px;top:607px;font-family:"Oswald",sans-serif;font-weight:600;font-size:18px;color:var(--accent)}
.shop-btn{left:56px;top:642px;width:105px;height:30px;background:var(--accent);color:#fff;font-weight:700;font-size:11.5px;display:flex;align-items:center;justify-content:center;letter-spacing:.3px}

.main-photo{left:427px;top:396px;width:310px;height:333px;background:linear-gradient(160deg,#a0793a 0%,#d7b47a 35%,#6b2e15 55%,#caa063 75%,#8c6a35 100%)}
.thumb{top:735px;width:74px;height:74px}
.t1{left:427px;background:linear-gradient(135deg,#c98836,#8a4c1a)}
.t2{left:505px;background:linear-gradient(135deg,#b4864e,#e2c08a)}
.t3{left:583px;background:linear-gradient(135deg,#7e5a3c,#c9a582)}
.t4{left:662px;background:linear-gradient(135deg,#3a2a20,#b08a5e)}

.review{left:272px;top:580px;width:222px;height:135px;background:#fff;box-shadow:0 4px 18px rgba(0,0,0,.1)}
.review-text{left:24px;top:28px;width:180px;font-size:8.9px;line-height:14.2px;color:var(--text)}
.review-stars{left:23px;top:90px}
.review-name{left:23px;top:103px;font-size:10.5px;font-weight:600;color:var(--accent);letter-spacing:.3px}
.review-arrows{left:174px;top:106px}

.footer{left:0;top:872px;width:798px;height:328px;background:var(--footer)}
.foot-brand{left:58px;top:950px;width:135px;height:92px;border:3px solid var(--bark);display:flex;align-items:center;justify-content:center;gap:6px}
.foot-brand .brand-mark{width:12px;height:12px}
.foot-brand .brand-name{font-size:16px}
.foot-head{top:944px;font-size:16px}
.foot-links{left:233px;top:970px;font-size:8.6px;line-height:16px;color:var(--muted)}
.foot-contact{left:360px;top:970px;font-size:8.6px;line-height:13px;color:var(--muted)}
.foot-contact .row{display:flex;gap:5px;margin-bottom:3px}
.socials{left:365px;top:1025px;display:flex;gap:14px}
.socials span{width:9px;height:9px;background:var(--accent);display:block}
.field{left:551px;width:162px;background:var(--field);font-size:7px;color:var(--muted);padding:7px 10px}
.submit{left:552px;top:1092px;width:61px;height:21px;background:var(--accent);color:#fff;font-size:7.5px;font-weight:700;display:flex;align-items:center;justify-content:center}
.rule{left:59px;top:1160px;width:680px;height:1px;background:var(--line)}
.to-top{left:753px;top:1149px;width:22px;height:22px;border-radius:50%;background:var(--bark)}
.copyright{left:0;top:1174px;width:798px;text-align:center;font-size:10.5px;color:var(--bark)}
</style>
</head>
<body>

<div class="abs topbar">
  <div class="abs note">Ordering larger quantities? Call us.</div>
  <div class="abs contact">
    <span><svg width="6" height="6" viewBox="0 0 10 10"><path d="M2 0l2 2-1 2c1 1 2 2 3 3l2-1 2 2-2 2C4 10 0 6 0 2z" fill="#c8782a"/></svg>phone number : &nbsp;+1 555 014 7730</span>
    <span><svg width="7" height="5" viewBox="0 0 12 9"><rect width="12" height="9" fill="#c8782a"/><path d="M0 0l6 5 6-5" stroke="#2b1608" fill="none"/></svg>Email : hello@movelterra.com, orders@movelterra.com</span>
  </div>
</div>

<header class="abs header">
  <div class="abs brand"><span class="brand-mark"></span><span class="brand-name">Movel Terra</span></div>
  <nav class="abs nav">
    <span>Home</span><span>Wall Paneling</span><span>Door</span><span class="active">Cutting Boards</span><span>Table Tops</span><span>About Us</span><span>Contact Us</span>
  </nav>
</header>

<section class="abs hero" role="img" aria-label="Café interior with reclaimed wood wall and wooden tables beside a colourful fishing boat"></section>
<h1 class="abs display hero-title">Table Tops</h1>

<h2 class="abs display made-title">How It's Made</h2>
<p class="abs made-copy">Our table tops are made out of reclaimed teak by local villagers. Each is finished with a food grade antibacterial coating that also helps maintain both the strength &amp; the flexibility of the wood fibers. Each table top is also water repellent, preventing oxidation and decay.</p>

<h3 class="abs display product-title">Slab Table Tops</h3>
<div class="abs rating">RATING: 5.00
  <svg width="10" height="10" viewBox="0 0 24 24"><path d="M12 1l3.4 7 7.6 1-5.5 5.3 1.3 7.6L12 18.3 5.2 21.9l1.3-7.6L1 9l7.6-1z" fill="var(--star)"/></svg>
</div>
<div class="abs specs">
  <p>GBRS: these boards may help qualify your project for GBRS points MR 4.1 &amp; 4.2 (Recycled Content) and EQ 4.4 (low VOC emission)</p>
  <p>TFC Certified: These products have a Chain-of-Custody TFC certification as well as the Timber Legality Verification by the VRT authority.</p>
  <p>Plank dimensions: L 47.75 x W 11.75 x T 0.75<br>Eco-conscious manufacturing.</p>
</div>
<div class="abs price">$5.99</div>
<div class="abs shop-btn">SHOP NOW</div>

<div class="abs main-photo" role="img" aria-label="Long reclaimed teak slab table top with dark grain streaks"></div>
<div class="abs thumb t1" role="img" aria-label="Round end-grain table top"></div>
<div class="abs thumb t2" role="img" aria-label="Round segmented wood table top"></div>
<div class="abs thumb t3" role="img" aria-label="Mixed plank table surface"></div>
<div class="abs thumb t4" role="img" aria-label="Slab counter in a shop"></div>

<div class="abs review">
  <p class="abs review-text">Lorem Ipsum is simply dummy text of the printing and typesetting industry. Lorem Ipsum has been the industry's standard dummy text.</p>
  <svg class="abs review-stars" width="58" height="10" viewBox="0 0 116 20">
    <g fill="var(--star)">
      <path id="s" d="M10 0l2.9 6 6.6.9-4.8 4.6 1.2 6.5L10 15l-5.9 3 1.2-6.5L.5 6.9 7.1 6z"/>
      <use href="#s" x="24"/><use href="#s" x="48"/><use href="#s" x="72"/><use href="#s" x="96"/>
    </g>
  </svg>
  <div class="abs review-name">Mara Quill</div>
  <svg class="abs review-arrows" width="26" height="10" viewBox="0 0 26 10"><path d="M5 1L1 5l4 4M21 1l4 4-4 4" stroke="var(--bark)" stroke-width="1.8" fill="none"/></svg>
</div>

<footer class="abs footer" role="img" aria-label="Light background patterned with faint tree ring circles"></footer>
<div class="abs foot-brand"><span class="brand-mark"></span><span class="brand-name">Movel Terra</span></div>

<h4 class="abs display foot-head" style="left:233px">Navigation</h4>
<div class="abs foot-links">Home<br>Wall panels<br>Doors<br>Cutting boards<br>About us</div>

<h4 class="abs display foot-head" style="left:360px">Contact Us</h4>
<div class="abs foot-contact">
  <div class="row"><svg width="8" height="8" viewBox="0 0 10 10"><path d="M2 0l2 2-1 2c1 1 2 2 3 3l2-1 2 2-2 2C4 10 0 6 0 2z" fill="var(--accent)"/></svg>Phone number +1 555 014 7730</div>
  <div class="row"><svg width="8" height="8" viewBox="0 0 12 10"><rect y="1" width="12" height="8" fill="var(--accent)"/><path d="M0 1l6 4 6-4" stroke="#fff" fill="none"/></svg><span>Email us : hello@movelterra.com,<br>orders@movelterra.com</span></div>
</div>
<div class="abs socials"><span></span><span></span><span></span></div>

<h4 class="abs display foot-head" style="left:550px">Contact Form</h4>
<div class="abs field" style="top:973px;height:22px">Name</div>
<div class="abs field" style="top:998px;height:21px">Email</div>
<div class="abs field" style="top:1022px;height:67px">Message</div>
<div class="abs submit">SUBMIT</div>

<div class="abs rule"></div>
<div class="abs to-top"><svg width="22" height="22" viewBox="0 0 22 22"><path d="M8 12l3-3 3 3" stroke="#fff" stroke-width="1.4" fill="none"/></svg></div>
<div class="abs copyright">Copyright 2020 | All Rights Reserved</div>

</body>
</html>
```